Business Card and Letterhead for Pimlu - modern real estate business

I need a double sided business card design for Pimlu. Please see business card brief here https://files.trelvonadocs.com/sheet/r/7QzTmWbaXLJnoPEd-kRyUgFhHsstbvCe2qfoMxDa_pz/view?mode=shared

Please feel free to design the business cards however you feel best. I am happy to give some creative freedoms and then provide feedback from there.

Please then also create a letterhead to match the business card design

Colors

Designer to choose colors to be used in the design.

Requirements
Must have
• Must be a modern, elegant business card which looks very professional

```html
<!DOCTYPE html>
<html lang="en">
<head>
<meta charset="utf-8">
<title>Pimlu Stationery – Letterhead and Business Card</title>
<link href="https://fonts.googleapis.com/css2?family=Montserrat:wght@400;500;600&family=Open+Sans:wght@400&display=swap" rel="stylesheet">
<style>
  :root {
    --backdrop: #a3b5bb;
    --brand-red: #e30613;
    --paper: #ffffff;
    --ink: #3a3a3a;
    --rule: #8a8a8a;
    --card-dark: #2f2f30;
    --card-text: #f2f2f2;
    --card-rule: #8c8c8c;
  }
  * { box-sizing: border-box; margin: 0; padding: 0; }
  html, body { width: 1200px; height: 800px; overflow: hidden; }
  body {
    position: relative;
    background: var(--backdrop);
    font-family: "Open Sans", Arial, sans-serif;
    color: var(--ink);
  }

  /* ---------- Letterhead ---------- */
  .letterhead {
    position: absolute; left: 147px; top: 66px; width: 523px; height: 667px;
    background: var(--paper);
    border-top: 3px solid var(--brand-red);
    box-shadow: 1px 2px 4px rgba(0,0,0,.25);
  }
  .letterhead__brand {
    position: absolute; left: 0; right: 0; top: 13px; text-align: center;
    font-family: "Montserrat", Arial, sans-serif; font-weight: 600;
    font-size: 27px; letter-spacing: 2px; color: var(--brand-red);
  }
  .letterhead__rule {
    position: absolute; left: 40px; right: 41px; top: 46px;
    height: 1px; background: var(--rule);
  }
  .letter {
    position: absolute; left: 57px; top: 182px; width: 410px;
    font-size: 8.3px; line-height: 19.6px; color: #444;
  }
  .letter__date { margin-bottom: 25px; }
  .letter__para { margin-bottom: 2px; }
  .signature {
    position: absolute; left: 362px; top: 468px; width: 100px; height: 34px;
    background: linear-gradient(90deg, rgba(80,80,80,.05), rgba(80,80,80,.18), rgba(80,80,80,.05));
    border-radius: 4px;
  }
  .signatory {
    position: absolute; left: 364px; top: 499px;
    font-size: 8.3px; line-height: 10px; color: #444;
  }
  .letterhead__footer-rule {
    position: absolute; left: 40px; right: 41px; top: 623px;
    height: 1px; background: var(--rule);
  }
  .letterhead__icons {
    position: absolute; left: 244px; top: 617px; width: 35px; height: 12px;
    background: var(--paper);
  }
  .letterhead__contacts {
    position: absolute; left: 0; right: 0; top: 632px; text-align: center;
    font-size: 8.3px; color: #333; word-spacing: 2px;
  }
  .letterhead__contacts span { margin: 0 5px; }
  .letterhead__band {
    position: absolute; left: 0; right: 0; bottom: 0; height: 16px;
    background: var(--brand-red); color: #fff;
    font-size: 7.5px; line-height: 16px; text-align: center;
  }

  /* ---------- Business card ---------- */
  .card {
    position: absolute; width: 345px; height: 197px;
    background: var(--card-dark);
    box-shadow: 1px 2px 4px rgba(0,0,0,.3);
    font-family: "Montserrat", Arial, sans-serif; color: var(--card-text);
  }
  .card--front { left: 708px; top: 306px; border-left: 2px solid var(--brand-red); }
  .card--back  { left: 707px; top: 537px; height: 196px; }
  .card__portrait {
    position: absolute; left: 0; top: 0; width: 156px; height: 197px;
    background: linear-gradient(180deg, #3a3a3b 0%, #4a4644 45%, #2a2a2b 100%);
  }
  .card__details {
    position: absolute; left: 162px; right: 6px; top: 28px; text-align: center;
  }
  .card__name {
    font-weight: 500; font-size: 14.5px; letter-spacing: 1.2px;
    color: var(--brand-red); line-height: 16px;
  }
  .card__role { font-size: 9.5px; line-height: 13px; margin-top: 0; }
  .card__icon-row {
    position: relative; height: 12px; margin: 14px auto 0; width: 80px;
  }
  .card__icon-row::before, .card__icon-row::after {
    content: ""; position: absolute; top: 6px; width: 20px; height: 1px; background: var(--card-rule);
  }
  .card__icon-row::before { left: 0; }
  .card__icon-row::after { right: 0; }
  .card__icon-row svg { position: absolute; left: 22px; top: 0; }
  .card__contacts { margin-top: 15px; font-size: 10.3px; line-height: 12px; }
  .card__rule { width: 80px; height: 1px; background: var(--card-rule); margin: 12px auto 0; }
  .card__address { font-size: 8.6px; margin-top: 15px; }
  .card__brand {
    position: absolute; left: 0; right: 0; top: 74px; text-align: center;
    font-weight: 600; font-size: 40px; letter-spacing: 3px; color: var(--brand-red);
  }
</style>
</head>
<body>

  <!-- Letterhead -->
  <section class="letterhead" aria-label="Pimlu letterhead">
    <div class="letterhead__brand">PIMLU</div>
    <div class="letterhead__rule"></div>

    <div class="letter">
      <p class="letter__date">Date, 10 September, 2020</p>
      <p class="letter__para">This is a sample letter that has been placed to demonstrate typing format (Your Company). letterhead design. When positioned properly, it will serve to work in harmony with all other elements letterhead. This letterhead design is meant to project an image</p>
      <p class="letter__para">This letterhead design is meant project an image of professionalism reliability. By using simple aligned we have created a very spacious feeling. The simplicity suggest strength the spaciousness contributes the aesthetics the layout. These basic qualities along with the (Your Company)</p>
      <p class="letter__para">look and helps reinforce the (Your Company) brand. letterhead design is meant to project an image of design. When positioned properly, it will serve to work in harmony all the other elements letterhead. professionalism and reliability.</p>
      <p class="letter__para">This letterhead design is based on the (Form of your logo) form (Your Company) logo. Each stationery we have created a very spacious feeling. The simplicity suggests strength the spaciousness contribute part of the (Form of your logo).</p>
    </div>

    <div class="signature" role="img" aria-label="Handwritten signature of Leo Hartwell"></div>
    <p class="signatory">Leo Hartwell<br>Manager</p>

    <div class="letterhead__footer-rule"></div>
    <svg class="letterhead__icons" viewBox="0 0 35 12" aria-hidden="true">
      <g fill="#e30613">
        <circle cx="6" cy="6" r="5"/><circle cx="17.5" cy="6" r="5"/><circle cx="29" cy="6" r="5"/>
      </g>
      <g fill="none" stroke="#fff" stroke-width="1">
        <path d="M4.3 3.6c.3 2 1.6 3.4 3.6 4" stroke-linecap="round"/>
        <rect x="15" y="4.2" width="5" height="3.6"/><path d="M15 4.2l2.5 2 2.5-2"/>
        <circle cx="29" cy="6" r="2.6"/><path d="M26.4 6h5.2M29 3.4v5.2"/>
      </g>
    </svg>
    <p class="letterhead__contacts"><span>0412 550 318</span><span>dana@pimlu.com</span><span>www.pimlu.com</span></p>
    <div class="letterhead__band">PO Box 1190, Larkfield NSW 2790</div>
  </section>

  <!-- Business card, front -->
  <section class="card card--front" aria-label="Business card front">
    <div class="card__portrait" role="img" aria-label="Portrait photo of Dana Merrow in a dark suit"></div>
    <div class="card__details">
      <p class="card__name">DANA MERROW</p>
      <p class="card__role">Licenced Real Estate Agent</p>
      <div class="card__icon-row">
        <svg width="36" height="12" viewBox="0 0 35 12" aria-hidden="true">
          <g fill="#e30613">
            <circle cx="6" cy="6" r="5"/><circle cx="17.5" cy="6" r="5"/><circle cx="29" cy="6" r="5"/>
          </g>
          <g fill="none" stroke="#fff" stroke-width="1">
            <path d="M4.3 3.6c.3 2 1.6 3.4 3.6 4" stroke-linecap="round"/>
            <rect x="15" y="4.2" width="5" height="3.6"/><path d="M15 4.2l2.5 2 2.5-2"/>
            <circle cx="29" cy="6" r="2.6"/><path d="M26.4 6h5.2M29 3.4v5.2"/>
          </g>
        </svg>
      </div>
      <p class="card__contacts">0412 550 318<br>dana@pimlu.com<br>www.pimlu.com</p>
      <div class="card__rule"></div>
      <p class="card__address">PO Box 1190, Larkfield NSW 2790</p>
    </div>
  </section>

  <!-- Business card, back -->
  <section class="card card--back" aria-label="Business card back">
    <div class="card__brand">PIMLU</div>
  </section>

</body>
</html>
```